Income Tax and Accounting Brochure

I need a brochure using my new logo (file attached). I do tax work and accounting work. I am an EA (QFB Enrolled Agent - logo attached) and would like this incorporated into the brochure. I also have a MSA in Accounting. Please incorporate the text that I have provided in the brochure.
Updates

Need extra days to review

Target Market(s)

Tax Clients - both business and individuals

Industry/Entity Type

Accounting

Colors
0054AA
0677BA
7BADD7
CADEEF
E8F1F8

Requirements
Must have
• Use my logo and the QFB EA file in the brochure
Nice to have
• I would like to see a brochure that I can customize with my own text if possible.

```html
<!DOCTYPE html>
<html lang="en">
<head>
<meta charset="utf-8">
<title>Harbor Line Accounting &amp; Consulting – Tax Brochure</title>
<link href="https://fonts.googleapis.com/css2?family=Rubik:ital,wght@0,400;0,500;0,600;1,400&display=swap" rel="stylesheet">
<style>
:root{
  --navy:#0054AA;
  --blue:#0677BA;
  --sky:#7BADD7;
  --mist:#CADEEF;
  --ice:#E8F1F8;
  --red:#C8102E;
  --ink:#1d1d1f;
  --stage:#e6e8eb;
  --paper:#ffffff;
}
*{box-sizing:border-box;margin:0;padding:0}
html,body{width:1200px;height:851px;overflow:hidden;background:var(--stage);font-family:"Rubik",sans-serif;color:var(--ink)}
.spread{position:relative;width:1200px;height:851px}
.page{position:absolute;top:30px;width:560px;height:792px;background:var(--paper);overflow:hidden;box-shadow:0 6px 18px rgba(0,0,0,.15)}
.page--front{left:20px}
.page--back{left:620px}

/* brand */
.brand{position:absolute;display:flex;align-items:center;gap:9px}
.brand__dot{width:52px;height:52px;border-radius:50%;background:var(--navy);flex:none}
.brand__name{color:var(--navy);font-weight:500;font-size:15px;line-height:1.3;letter-spacing:1.6px;text-transform:uppercase}
.page--front .brand{top:30px;right:36px}
.page--back .brand{top:42px;left:50%;transform:translateX(-50%)}
.page--back .brand__dot{width:60px;height:60px}
.page--back .brand__name{font-size:16.5px}

/* front */
.front-art{position:absolute;left:0;top:0;width:560px;height:560px}
.portrait{position:absolute;left:337px;top:289px;width:154px;height:154px;border-radius:50%;background:radial-gradient(circle at 50% 45%,#c9a27f 0,#8d6a52 55%,#2d2a2c 100%);border:3px solid #fff}
.principal{position:absolute;right:61px;top:468px;text-align:right}
.principal__name{color:var(--navy);font-weight:600;font-size:15.5px}
.principal__role{color:var(--red);font-style:italic;font-size:15px;margin-top:1px;margin-right:50px}
.bio{position:absolute;left:57px;top:545px;width:442px;font-size:10.5px;line-height:14.2px;text-align:justify}
.bio p+p{margin-top:14px}
.contact-bar{position:absolute;left:42px;top:716px;width:472px;height:41px;background:var(--navy);color:#fff;display:flex;align-items:center;justify-content:center;gap:8px;font-weight:500;font-size:16px}
.contact-bar svg{width:17px;height:17px;flex:none}
.contact-bar .gap{width:4px}

/* back */
.content{position:absolute;left:51px;top:140px;width:459px}
.section-head{height:25px;background:linear-gradient(90deg,var(--navy),var(--blue));color:#fff;display:flex;align-items:center;font-weight:600;font-size:14.6px;position:relative;padding-left:35px}
.section-head::before{content:"";position:absolute;left:0;top:-1px;width:27px;height:27px;border-radius:50%;background:var(--paper);border:4px solid var(--navy)}
.copy{font-size:10.5px;line-height:14.2px;text-align:justify}
.copy p+p{margin-top:14px}
.copy strong{font-weight:500}
.intro{margin-top:11px}
.benefits{list-style:none;margin-top:14px;position:relative}
.benefits li{position:relative;padding-left:18px;font-size:10.5px;line-height:14.2px;text-align:justify}
.benefits li+li{margin-top:14px}
.benefits li::after{content:"";position:absolute;left:5px;top:14px;bottom:-12px;width:1px;background:var(--sky)}
.benefits li:last-child::after{display:none}
.benefits svg{position:absolute;left:0;top:2px;width:11px;height:11px}
.head-2{margin-top:13px}
.head-3{margin-top:13px}
.books{margin-top:14px}
.footer-art{position:absolute;left:0;top:640px;width:560px;height:152px}
.footer{position:absolute;left:44px;top:724px;right:51px;display:flex;justify-content:space-between;color:#fff}
.footer__address{font-size:11.6px;line-height:14.3px}
.footer__address strong{font-weight:500}
.footer__reach{text-align:right}
.footer__line{display:flex;align-items:center;justify-content:flex-end;gap:8px;font-weight:500}
.footer__line--phone{font-size:26px;line-height:26px}
.footer__line--web{font-size:17px;margin-top:2px}
.footer__line svg{width:16px;height:16px}
</style>
</head>
<body>
<main class="spread">

  <!-- Front page -->
  <section class="page page--front">
    <svg class="front-art" viewBox="0 0 560 560" aria-hidden="false">
      <defs>
        <linearGradient id="photoTone" x1="0" y1="0" x2="1" y2="1">
          <stop offset="0" stop-color="#8a7c72"/>
          <stop offset=".45" stop-color="#cfcac6"/>
          <stop offset="1" stop-color="#e4e1de"/>
        </linearGradient>
      </defs>
      <path role="img" aria-label="Photo of an accountant working a calculator over invoices at a desk" d="M0 94 Q300 112 560 258 L560 398 Q250 400 0 520 Z" fill="url(#photoTone)"/>
      <path d="M20 80 Q320 96 560 244" fill="none" stroke="var(--navy)" stroke-width="9"/>
      <path d="M0 92 Q300 108 548 252" fill="none" stroke="var(--red)" stroke-width="8"/>
      <path d="M300 428 Q430 398 560 394 L560 380 Q430 382 300 428 Z" fill="var(--red)"/>
      <path d="M0 520 Q250 402 560 390 L560 400 Q260 412 0 538 Z" fill="var(--navy)"/>
    </svg>
    <div class="portrait" role="img" aria-label="Portrait photo of the principal"></div>

    <div class="brand">
      <span class="brand__dot"></span>
      <span class="brand__name">Harbor Line Accounting<br>&amp; Consulting, LLC</span>
    </div>

    <div class="principal">
      <div class="principal__name">Maren J Holloway, MSA EA</div>
      <div class="principal__role">(Principal)</div>
    </div>

    <div class="bio">
      <p>I have a Masters' Degree in accounting and am an QFB Enrolled Agent. I am also a LedgerBooks Advanced Certified Consultant in both the online and desktop products including Enterprise and Point of Sale. I provide individual and small business tax services, Accounting, bookkeeping, QFB representation, insurance audit representation, business license assistance and more.</p>
      <p>I have experience working with a wide variety of clients from the point where they first decide they want to start a business. They are often unsure about what to do first- I have a lot of experience to offer you.</p>
    </div>

    <div class="contact-bar">
      <svg viewBox="0 0 24 24" fill="none" stroke="#fff" stroke-width="2"><path d="M5 3h4l2 5-2.5 1.5a11 11 0 0 0 6 6L16 13l5 2v4a2 2 0 0 1-2 2A16 16 0 0 1 3 5a2 2 0 0 1 2-2z"/></svg>
      <span>(555)014-2290</span>
      <span class="gap"></span>
      <svg viewBox="0 0 24 24" fill="none" stroke="#fff" stroke-width="1.6"><circle cx="12" cy="12" r="9"/><path d="M3 12h18M12 3c3 3 3 15 0 18M12 3c-3 3-3 15 0 18"/></svg>
      <span>WWW.HARBORLINEACCT.COM</span>
    </div>
  </section>

  <!-- Back page -->
  <section class="page page--back">
    <div class="brand">
      <span class="brand__dot"></span>
      <span class="brand__name">Harbor Line Accounting<br>&amp; Consulting, LLC</span>
    </div>

    <div class="content">
      <h2 class="section-head">What a joy it is to watch success in action!</h2>
      <div class="copy intro">
        <p><strong>Tax Preparation – why hire us?</strong><br>Preparing your own income tax return can be a task that leaves you with more questions than answers. According to a study released by the National Accounting Review Office last year, most taxpayers (77% of 71 million taxpayers) believe they benefited from using a professional tax preparer.</p>
        <p>Whether we like it or not, today's tax laws are so complicated that filing a relatively simple return can be confusing. It is just too easy to overlook deductions and credits to which you are entitled. Even if you use a computer software program there's no substitute for the assistance of an experienced tax professional.</p>
      </div>

      <h2 class="section-head head-2">Here's what your get...</h2>
      <ul class="benefits">
        <li><svg viewBox="0 0 12 12"><circle cx="6" cy="6" r="6" fill="var(--red)"/><path d="M3.2 6.2l2 2 3.6-4" fill="none" stroke="#fff" stroke-width="1.5"/></svg>Your tax return will be checked and rechecked by our computer software identifying potential problems the QFB may look at more closely and reviewing the math to limit QFB contacts.</li>
        <li><svg viewBox="0 0 12 12"><circle cx="6" cy="6" r="6" fill="var(--red)"/><path d="M3.2 6.2l2 2 3.6-4" fill="none" stroke="#fff" stroke-width="1.5"/></svg>Your tax return can be filed electronically so you will get a refund back quicker.</li>
        <li><svg viewBox="0 0 12 12"><circle cx="6" cy="6" r="6" fill="var(--red)"/><path d="M3.2 6.2l2 2 3.6-4" fill="none" stroke="#fff" stroke-width="1.5"/></svg>Our staff will show you how to adjust your payroll withholding to get more money back each week. Why give the QFB an interest free loan for up to 16 months.</li>
        <li><svg viewBox="0 0 12 12"><circle cx="6" cy="6" r="6" fill="var(--red)"/><path d="M3.2 6.2l2 2 3.6-4" fill="none" stroke="#fff" stroke-width="1.5"/></svg>We will show you potential deductions to limit your tax liability for next year. In addition, we will give you a sheet of commonly overlooked deductions to limit the following year's tax liability.</li>
      </ul>

      <h2 class="section-head head-3">Books a Mess: No Problem!</h2>
      <div class="copy books">
        <p>If you own a small business and haven't kept up your bookkeeping, don't worry. We can help you. We'll prepare your bookkeeping for the year, prepare a full Schedule C, as well as your personal income tax return. Then we'll help you set up an easy system that allows you to keep your books in tip-top shape next year.</p>
      </div>
    </div>

    <svg class="footer-art" viewBox="0 0 560 152" aria-hidden="true">
      <defs>
        <linearGradient id="footTone" x1="0" y1="0" x2="1" y2="0">
          <stop offset="0" stop-color="var(--navy)"/>
          <stop offset="1" stop-color="var(--blue)"/>
        </linearGradient>
      </defs>
      <path d="M0 46 Q300 70 560 16 L560 30 Q300 76 0 52 Z" fill="var(--red)"/>
      <path d="M0 52 Q300 78 560 30 L560 152 L0 152 Z" fill="url(#footTone)"/>
    </svg>
    <div class="footer">
      <div class="footer__address">
        <strong>Harbor Line Accounting &amp; Consulting, LLC</strong><br>
        2870 Fenwick Mill Rd, PO Box 41<br>
        Alderby, VA 20000
      </div>
      <div class="footer__reach">
        <div class="footer__line footer__line--phone">
          <svg viewBox="0 0 24 24" fill="none" stroke="#fff" stroke-width="2"><path d="M5 3h4l2 5-2.5 1.5a11 11 0 0 0 6 6L16 13l5 2v4a2 2 0 0 1-2 2A16 16 0 0 1 3 5a2 2 0 0 1 2-2z"/></svg>
          <span>(555)014-2290</span>
        </div>
        <div class="footer__line footer__line--web">
          <svg viewBox="0 0 24 24" fill="none" stroke="#fff" stroke-width="1.6"><circle cx="12" cy="12" r="9"/><path d="M3 12h18M12 3c3 3 3 15 0 18M12 3c-3 3-3 15 0 18"/></svg>
          <span>HARBORLINEACCT.COM</span>
        </div>
      </div>
    </div>
  </section>

</main>
</body>
</html>
```